Oil Field Service company needs professional business cards

Looking to clean up our current company business cards and look a little more professional. Brenwick Casing Services is a US based company that services the oil field. We deal with engineers, managers and oil rigs....................................................................................................................................................................................................................................................................................................................................................................................................

Target Market(s)

Oil and Gas professionals

Industry/Entity Type

Oil And Gas

Contact Information for Business Card

See attached photo as example

Font styles to use
Sans Serif

Colors
ec1f27

Requirements
Must have
• Company Logo, Name, Title, Cell, Office, Fax, Email.
• See attached photo
Nice to have
• External CRT, Internal CRT, Casing Crews, Torque Turn, Laydown Machine
Should not have
• Do not introduce any new pictures and keep it professional looking

```html
<!DOCTYPE html>
<html lang="en">
<head>
<meta charset="utf-8">
<title>Brenwick Casing Services – Business Card</title>
<link rel="stylesheet" href="https://fonts.googleapis.com/css2?family=Open+Sans:wght@400;600;700;800&display=swap">
<style>
  :root {
    --brand-red: #ec1f27;
    --slate: #45545f;
    --slate-text: #4a4f55;
    --paper: #ffffff;
    --stage: #4b4b4b;
    --divider: #c9cdd1;
  }
  * { box-sizing: border-box; margin: 0; padding: 0; }
  html, body {
    width: 1105px; height: 1200px; overflow: hidden;
    background: var(--stage);
    font-family: "Open Sans", Arial, sans-serif;
  }
  .canvas { position: relative; width: 1105px; height: 1200px; }

  .card { position: absolute; left: 196px; width: 720px; height: 411px; }

  /* Front */
  .card-front { top: 145px; background: var(--paper); overflow: hidden; }
  .front-swoop { position: absolute; left: 0; top: 0; width: 720px; height: 40px; }
  .front-base { position: absolute; left: 0; bottom: 0; width: 100%; height: 12px; background: var(--slate); }

  .wordmark { position: absolute; text-align: center; color: var(--slate); font-weight: 800; line-height: 1; }
  .wordmark .name-main { display: block; letter-spacing: 1px; }
  .wordmark .name-sub { display: block; letter-spacing: 3px; }
  .card-front .wordmark { left: 60px; top: 178px; width: 290px; }
  .card-front .name-main { font-size: 50px; }
  .card-front .name-sub { font-size: 17px; margin-top: 12px; }

  .front-divider { position: absolute; left: 381px; top: 93px; width: 1px; height: 243px; background: var(--divider); }

  .contact { position: absolute; left: 413px; top: 92px; color: var(--slate-text); }
  .contact .person { font-size: 28px; font-weight: 600; color: var(--brand-red); line-height: 1.2; }
  .contact .role { font-size: 20px; line-height: 1.3; }
  .contact .location { font-size: 20px; margin-top: 14px; margin-bottom: 10px; }
  .contact-list { list-style: none; }
  .contact-list li { display: flex; align-items: center; font-size: 19px; height: 27.5px; }
  .contact-list svg { width: 16px; height: 16px; margin-right: 10px; flex: none; fill: var(--brand-red); }

  /* Back */
  .card-back { top: 602px; background: var(--slate); }
  .card-back .wordmark { left: 0; top: 155px; width: 720px; color: var(--paper); }
  .card-back .name-main { font-size: 56px; }
  .card-back .name-sub { font-size: 21px; margin-top: 14px; }
  .services { position: absolute; left: 0; top: 320px; width: 720px; text-align: center; color: var(--paper); font-size: 19px; line-height: 27px; }
</style>
</head>
<body>
<div class="canvas">
  <section class="card card-front">
    <svg class="front-swoop" viewBox="0 0 720 40" preserveAspectRatio="none" aria-hidden="true">
      <path d="M0 0 H720 V2 C560 4 470 30 360 30 C250 30 160 4 0 2 Z" fill="var(--brand-red)"/>
    </svg>

    <div class="wordmark">
      <span class="name-main">BRENWICK</span>
      <span class="name-sub">CASING SERVICES</span>
    </div>

    <div class="front-divider"></div>

    <div class="contact">
      <p class="person">Cody Harlan</p>
      <p class="role">Area Manager</p>
      <p class="location">Fairview, OK 73737</p>
      <ul class="contact-list">
        <li><svg viewBox="0 0 16 16"><path d="M3.5 1 L6 4 L4.6 5.8 C5.4 7.8 8 10.5 10.2 11.4 L12 10 L15 12.5 L13.4 15 C7 14.6 1.4 9 1 2.6 Z"/></svg>(555)204-1180</li>
        <li><svg viewBox="0 0 16 16"><path d="M4 0 H12 V16 H4 Z M5.5 2 V12 H10.5 V2 Z M7 13 H9 V14.5 H7 Z" fill-rule="evenodd"/></svg>(555)317-6642</li>
        <li><svg viewBox="0 0 16 16"><path d="M4 1 H12 V5 H4 Z M1 6 H15 V15 H1 Z M3 10 H13 V11.5 H3 Z" fill-rule="evenodd"/></svg>(555)204-1193</li>
        <li><svg viewBox="0 0 16 16"><path d="M1 3 H15 V13 H1 Z M1.5 3.5 L8 9 L14.5 3.5" /><path d="M1.5 3.8 L8 9 L14.5 3.8" stroke="#fff" stroke-width="1.4" fill="none"/></svg>cody@brenwick.com</li>
        <li><svg viewBox="0 0 16 16"><circle cx="8" cy="8" r="7"/><path d="M5 4 C7 5 6 7 8 8 C9 10 7 12 8 14 M10 3 C11 5 13 5 14 7" stroke="#fff" stroke-width="1.3" fill="none"/></svg>www.brenwick.com</li>
      </ul>
    </div>

    <div class="front-base"></div>
  </section>

  <section class="card card-back">
    <div class="wordmark">
      <span class="name-main">BRENWICK</span>
      <span class="name-sub">CASING SERVICES</span>
    </div>
    <p class="services">External CRT &nbsp;|&nbsp; Internal CRT &nbsp;|&nbsp; Casing Crews<br>Torque Turn &nbsp;|&nbsp; Laydown Machine</p>
  </section>
</div>
</body>
</html>
```